Physiotherapist for Horse and Rider

I need a web design and a working, functioning website for my profession as physiotherapist. Tabs available for the therapy I offer such a massage, stretching, taping, elektrotherapie en advies. Another tab for introducing myself and one for workshops I want to give. I like a tab for photo's and one for how the clients can contact me.

I like it similar too velarun.be Not too much text to read, a beautifull design with matching colours and nice photo's.

Target Market(s)

horse people

Industry/Entity Type

Massage

Number of Pages Required

1 page

Font styles to use
Serif
Script

Colors
34a6d7
0355a3
0493ce

Requirements
Must have
• I like the blue colours from my logo design.
• Contact with e-mail.
• domain name Trotvale Soin
Nice to have
• some off the photo's I uploaded

```html
<!DOCTYPE html>
<html lang="en">
<head>
<meta charset="utf-8">
<title>Trotvale Soin – Physiotherapy for Horse and Rider</title>
<link rel="stylesheet" href="https://fonts.googleapis.com/css2?family=Open+Sans:wght@400;600;700&family=Roboto+Condensed:wght@700&family=Lobster&display=swap">
<style>
:root{
  --blue-light:#34a6d7;
  --blue-deep:#0355a3;
  --blue-mid:#0493ce;
  --blue-band:#1d5fb0;
  --ink:#333;
  --muted:#555;
  --dark:#141414;
  --footer-bg:#efefef;
  --white:#fff;
}
*{box-sizing:border-box;margin:0;padding:0}
html,body{width:1200px;height:3197px;overflow:hidden}
body{position:relative;font-family:"Open Sans",Arial,sans-serif;color:var(--ink);background:var(--white)}
.abs{position:absolute}

/* Header */
.site-header{position:absolute;top:0;left:0;width:1200px;height:113px;background:var(--white);z-index:5}
.brand{position:absolute;left:88px;top:0;width:170px;height:150px;background:var(--white);border-radius:0 0 85px 85px;display:flex;flex-direction:column;align-items:center;justify-content:center;z-index:6}
.brand-mark{width:14px;height:14px;border-radius:50%;background:var(--blue-deep);margin-bottom:8px}
.brand-name{font-family:"Open Sans",Arial,sans-serif;font-weight:600;font-size:21px;color:var(--blue-deep)}
.topbar{position:absolute;right:52px;top:14px;display:flex;gap:28px;font-size:13px;color:var(--ink)}
.topbar .item{display:flex;align-items:center;gap:10px}
.topbar b{font-weight:700}
.round-ic{width:36px;height:36px;border-radius:50%;background:var(--blue-deep);display:flex;align-items:center;justify-content:center}
.main-nav{position:absolute;right:24px;top:66px;display:flex;gap:6px;font-size:14.5px}
.main-nav a{color:var(--ink);text-decoration:none;padding:6px 12px;border-radius:3px}
.main-nav a.active{background:var(--blue-deep);color:var(--white);font-weight:700}

/* Hero */
.hero{position:absolute;top:113px;left:0;width:1200px;height:570px;background:linear-gradient(100deg,#2c2620 0%,#4a3a2c 30%,#6d5a46 55%,#8a8277 75%,#6e6a64 100%)}
.hero-text{position:absolute;left:86px;top:323px;color:var(--white)}
.hero-text h1{font-family:"Roboto Condensed",Arial,sans-serif;font-size:34px;font-weight:700;letter-spacing:.3px}
.hero-text p{font-size:14.5px;line-height:22px;width:620px;margin-top:10px}
.btn{display:inline-block;background:var(--blue-mid);color:var(--white);font-weight:700;font-size:13px;text-align:center;border-radius:3px;text-transform:uppercase}
.hero .btn{position:absolute;left:86px;top:428px;width:118px;height:44px;line-height:44px}
.dots{position:absolute;left:566px;top:578px;display:flex;gap:7px}
.dots span{width:11px;height:11px;border-radius:50%;border:2px solid var(--white)}
.dots span.on{background:var(--blue-light);border-color:var(--blue-light)}

/* Section headings */
.sec-mark{width:44px;height:44px;border-radius:50%;margin:0 auto}
.sec-title{font-size:27px;font-weight:600;text-align:center;text-transform:uppercase;letter-spacing:.5px}

/* About */
.about{position:absolute;top:690px;left:0;width:1200px;text-align:center}
.about .sec-mark{background:var(--blue-deep);margin-top:12px}
.about .sec-title{color:var(--blue-mid);margin-top:18px}
.about .sec-title span{color:var(--blue-deep)}
.about p{width:830px;margin:22px auto 0;font-size:13px;line-height:26px;color:var(--muted)}
.about .btn{margin-top:28px;width:116px;height:46px;line-height:46px;box-shadow:0 3px 0 var(--blue-deep)}

/* Treatments */
.treatments{position:absolute;top:1040px;left:0;width:1200px;height:637px;background:linear-gradient(135deg,#1f4f99 0%,#2a6bc0 50%,#1b58a8 100%);color:var(--white);text-align:center}
.treatments .sec-mark{background:var(--white);margin-top:72px}
.treatments .sec-title{margin-top:18px;font-size:26px}
.cards{position:absolute;top:205px;left:88px;width:1024px;display:flex;justify-content:space-between}
.card{width:240px;text-align:center}
.card .photo{width:226px;height:226px;border-radius:50%;border:6px solid #d5d9df;margin:0 auto;background:radial-gradient(circle at 45% 45%,#b69273 0%,#6a4c36 55%,#3c3026 100%)}
.card h3{font-family:"Lobster",Georgia,serif;font-weight:400;font-size:23px;margin-top:20px}
.card p{font-size:12.5px;line-height:21px;margin-top:4px;height:44px}
.card .btn{margin-top:14px;width:104px;height:36px;line-height:36px;font-size:11px}
.arrow{position:absolute;top:310px;color:var(--white)}

/* Workshops */
.workshops{position:absolute;top:1740px;left:0;width:1200px;text-align:center}
.workshops .sec-mark{background:var(--blue-deep)}
.workshops .sec-title{color:var(--blue-mid);margin-top:18px}
.workshops .intro{width:760px;margin:16px auto 0;font-size:13px;line-height:26px;color:var(--muted)}
.ws-grid{position:absolute;top:188px;left:88px;width:1025px;display:flex;justify-content:space-between}
.ws{width:497px}
.ws .photo{height:239px;border-radius:3px;position:relative}
.ws:first-child .photo{background:linear-gradient(100deg,#4c3a2c,#7a6652 55%,#9a8e80)}
.ws:last-child .photo{background:linear-gradient(100deg,#8d8a86,#5f4f43 50%,#2c241e)}
.ws .frame{position:absolute;inset:10px;border:1px solid rgba(255,255,255,.6)}
.ws .zoom{position:absolute;left:228px;top:99px;width:40px;height:40px;border:2px solid var(--white);border-radius:50%;display:flex;align-items:center;justify-content:center}
.ws h4{margin-top:26px;color:var(--blue-mid);font-size:16px;font-weight:600;text-transform:uppercase;letter-spacing:.5px}

/* Contact */
.contact{position:absolute;top:2290px;left:0;width:1200px;height:470px;background:var(--dark)}
.contact h2{position:absolute;top:60px;width:100%;text-align:center;color:var(--white);font-size:27px;font-weight:600;text-transform:uppercase}
.field{position:absolute;background:var(--white);border-radius:3px;font-size:13px;color:var(--ink);padding:13px 18px}
.contact .btn{position:absolute;left:545px;top:343px;width:110px;height:44px;line-height:44px;font-size:14px;display:flex;align-items:center;justify-content:center;gap:8px}

/* Footer */
.site-footer{position:absolute;top:2760px;left:0;width:1200px;height:437px;background:var(--footer-bg)}
.col{position:absolute;top:92px}
.col h5{font-size:17px;font-weight:600;text-transform:uppercase;color:var(--ink);letter-spacing:.3px}
.col ul{list-style:none;margin-top:22px}
.col li{font-size:12.5px;color:var(--ink);height:33px;display:flex;gap:14px}
.col li .chev{color:var(--ink);font-weight:700;font-size:12px}
.contact-list li{height:auto;margin-bottom:18px;line-height:20px;gap:16px}
.socials{position:absolute;left:88px;top:272px;display:flex;gap:9px}
.socials span{width:33px;height:33px;border-radius:50%;background:var(--blue-deep)}
.newsletter .inp{width:273px;height:40px;background:var(--white);border:1px solid #d8d8d8;border-radius:3px;font-size:12px;padding:11px 16px;margin-top:0}
.newsletter .inp+.inp{margin-top:13px}
.newsletter .btn{margin-top:13px;width:99px;height:40px;line-height:40px;font-size:12px}
.rule{position:absolute;left:88px;top:368px;width:1025px;height:1px;background:#ccc}
.copy{position:absolute;top:400px;width:100%;text-align:center;font-size:12px;color:var(--ink)}
</style>
</head>
<body>

<header class="site-header">
  <div class="brand">
    <span class="brand-mark"></span>
    <span class="brand-name">Trotvale Soin</span>
  </div>
  <div class="topbar">
    <div class="item">
      <span class="round-ic"><svg width="16" height="16" viewBox="0 0 24 24"><path fill="#fff" d="M6.6 10.8a15.1 15.1 0 0 0 6.6 6.6l2.2-2.2c.3-.3.7-.4 1-.2 1.1.4 2.3.6 3.6.6.6 0 1 .4 1 1V20c0 .6-.4 1-1 1A17 17 0 0 1 3 4c0-.6.4-1 1-1h3.5c.6 0 1 .4 1 1 0 1.3.2 2.5.6 3.6.1.3 0 .7-.2 1z"/></svg></span>
      <span><b>CALL US :</b> (555)-214-0937</span>
    </div>
    <div class="item">
      <span class="round-ic"><svg width="16" height="14" viewBox="0 0 24 20"><path fill="#fff" d="M2 2h20v16H2zM3 3.5v1l9 6 9-6v-1z"/></svg></span>
      <span><b>MAIL US :</b> hello@trotvalesoin.be</span>
    </div>
  </div>
  <nav class="main-nav">
    <a class="active" href="#">Home</a>
    <a href="#">About Us</a>
    <a href="#">Massage</a>
    <a href="#">Stretching</a>
    <a href="#">Taping</a>
    <a href="#">Elektrotherapie En Advies</a>
    <a href="#">Photos</a>
    <a href="#">Contact Us</a>
  </nav>
</header>

<section class="hero" role="img" aria-label="Photo of the physiotherapist with her hand on a dark brown horse in a stable">
  <div class="hero-text">
    <h1>PHYSIOTHERAPY FOR HORSE AND RIDER</h1>
    <p>A horse feels a fly sitting on his coat. The smallest imbalance in muscle tone so he can feel his rider. Horse and rider influence each other, so I treat both in order</p>
  </div>
  <span class="btn">Read More</span>
  <div class="dots"><span class="on"></span><span></span><span></span><span></span></div>
</section>
<svg class="abs" style="left:0;top:590px" width="1200" height="100" viewBox="0 0 1200 100" aria-hidden="true">
  <path d="M0 58 C300 110 700 20 1200 0 L1200 100 L0 100Z" fill="#0355a3"/>
  <path d="M0 64 C300 112 700 32 1200 16 L1200 100 L0 100Z" fill="#fff"/>
  <path d="M0 72 C300 116 700 42 1200 26 L1200 31 C700 48 300 122 0 80Z" fill="#0493ce"/>
</svg>

<section class="about">
  <div class="sec-mark"></div>
  <h2 class="sec-title">About <span>&nbsp;Marthe Delvoort</span></h2>
  <p>Marthe Delvoort, 32 years, Trotvale Soin. Marthe graduated from the University of Northbridge as Human physiotherapist in 2007. She immediately began training Dierfysiotherapie in Faculty of Veterinary Medicine, Halvermoor and graduated as a physiotherapist for horses in 2010. She combines both the Physiotherapist for Horse and Rider. From year to year they schooled themselves in Human Manual Therapy. In year she learned natural hoof trimming. Since 2016 she has also engrossed in the Manual Taping Concept and Equitaping.</p>
  <span class="btn">Read More</span>
</section>

<section class="treatments">
  <div class="sec-mark"></div>
  <h2 class="sec-title">Treatments</h2>
  <svg class="arrow" style="left:40px" width="14" height="20" viewBox="0 0 14 20"><path d="M11 2 3 10l8 8" stroke="#fff" stroke-width="3" fill="none"/></svg>
  <svg class="arrow" style="left:1146px" width="14" height="20" viewBox="0 0 14 20"><path d="M3 2l8 8-8 8" stroke="#fff" stroke-width="3" fill="none"/></svg>
  <div class="cards">
    <div class="card">
      <div class="photo" role="img" aria-label="Photo of a horse receiving a head massage"></div>
      <h3>Massage</h3>
      <p>Heeft als doel de spieren te ontspannen en te versoepelen, de bloed</p>
      <span class="btn">Read More &#10140;</span>
    </div>
    <div class="card">
      <div class="photo" role="img" aria-label="Photo of a horse's leg being stretched"></div>
      <h3>Stretching</h3>
      <p>Houdt de spieren en de pezen soepel en op lengte. Na een spierscheur</p>
      <span class="btn">Read More &#10140;</span>
    </div>
    <div class="card">
      <div class="photo" role="img" aria-label="Photo of electrotherapy on a horse"></div>
      <h3>Elektrotherapie</h3>
      <p>Pijnstillende TENS, geeft kleine trillingen in de spiervezels waardoor spannen.</p>
      <span class="btn">Read More &#10140;</span>
    </div>
    <div class="card">
      <div class="photo" role="img" aria-label="Photo of taping being applied to a dark horse"></div>
      <h3>Taping</h3>
      <p>Door in van spieren te tapen, kan je de spier helpen ontspannen of net</p>
      <span class="btn">Read More &#10140;</span>
    </div>
  </div>
</section>

<section class="workshops">
  <div class="sec-mark"></div>
  <h2 class="sec-title">Workshops</h2>
  <p class="intro">There are many variations of passages of Lorem Ipsum available, but the majority have suffered alteration in some form, by injected humour, or randomised words which don't look even slightly believable.</p>
  <div class="ws-grid">
    <div class="ws">
      <div class="photo" role="img" aria-label="Photo of a woman massaging a bay horse">
        <span class="frame"></span>
        <span class="zoom"><svg width="16" height="16" viewBox="0 0 16 16"><circle cx="6.5" cy="6.5" r="4.5" stroke="#fff" stroke-width="2" fill="none"/><path d="M10 10l4 4" stroke="#fff" stroke-width="2"/></svg></span>
      </div>
      <h4>Zelf je paard masseren</h4>
    </div>
    <div class="ws">
      <div class="photo" role="img" aria-label="Photo of a woman treating a dark horse's neck"></div>
      <h4>Wellnessweekend voor paard en ruiter</h4>
    </div>
  </div>
</section>

<section class="contact">
  <h2>Contact Me</h2>
  <div class="field" style="left:261px;top:135px;width:332px;height:46px">Name</div>
  <div class="field" style="left:261px;top:194px;width:332px;height:46px">Email address</div>
  <div class="field" style="left:261px;top:253px;width:332px;height:46px">Phone number</div>
  <div class="field" style="left:608px;top:135px;width:332px;height:164px">Message</div>
  <span class="btn"><svg width="14" height="14" viewBox="0 0 24 24"><path fill="#fff" d="M2 11 22 2l-7 20-4-8z"/></svg>SEND</span>
</section>
<svg class="abs" style="left:0;top:2690px" width="1200" height="80" viewBox="0 0 1200 80" aria-hidden="true">
  <path d="M0 0 C300 70 800 80 1200 10 L1200 80 L0 80Z" fill="#0355a3"/>
  <path d="M0 10 C300 76 800 86 1200 22 L1200 80 L0 80Z" fill="#fff"/>
  <path d="M0 16 C300 82 800 92 1200 30 L1200 80 L0 80Z" fill="#0493ce"/>
  <path d="M0 24 C300 88 800 96 1200 38 L1200 80 L0 80Z" fill="#efefef"/>
</svg>

<footer class="site-footer">
  <div class="col" style="left:92px">
    <h5>Contact Us</h5>
    <ul class="contact-list">
      <li><svg width="16" height="14" viewBox="0 0 16 14"><path d="M8 0 0 7h2v7h4V9h4v5h4V7h2z" fill="#333"/></svg><span>1.10.32 of de Finibus Bonorum et<br>Malorum</span></li>
      <li><svg width="16" height="16" viewBox="0 0 16 16"><rect x="4" y="1" width="8" height="14" rx="1.5" stroke="#333" stroke-width="1.6" fill="none"/></svg><span>Call Us : (555)-214-0937</span></li>
      <li><svg width="16" height="14" viewBox="0 0 16 14"><rect x="1" y="2" width="14" height="10" stroke="#333" stroke-width="1.5" fill="none"/><path d="M1 2l7 5 7-5" stroke="#333" stroke-width="1.5" fill="none"/></svg><span>Mail Us: hello@trotvalesoin.be</span></li>
    </ul>
  </div>
  <div class="socials"><span></span><span></span><span></span><span></span><span></span></div>
  <div class="col" style="left:411px">
    <h5>Quick Links</h5>
    <ul><li><span class="chev">&raquo;</span>Home</li><li><span class="chev">&raquo;</span>About us</li><li><span class="chev">&raquo;</span>Massage</li><li><span class="chev">&raquo;</span>Stretching</li><li><span class="chev">&raquo;</span>Taping</li></ul>
  </div>
  <div class="col" style="left:624px">
    <h5>Other Links</h5>
    <ul><li><span class="chev">&raquo;</span>Terms of Use</li><li><span class="chev">&raquo;</span>Privacy Policy</li><li><span class="chev">&raquo;</span>Contact</li><li><span class="chev">&raquo;</span>Site map</li><li><span class="chev">&raquo;</span>Performance</li></ul>
  </div>
  <div class="col newsletter" style="left:838px">
    <h5>Our Newsletter</h5>
    <div style="margin-top:22px">
      <div class="inp">Enter Name</div>
      <div class="inp">Enter Email</div>
      <span class="btn">Subscribe</span>
    </div>
  </div>
  <div class="rule"></div>
  <p class="copy">@copyright 2017 Trotvale Soin.All Rights Reserved</p>
</footer>

</body>
</html>
```